Redesign business cards

We have a new logo and I am not that happy with the layout of our existing card and looking for a change. Font is a bit small and the green can be hard to read. Logo may need a tidy up as the copy I have is not that hi-res too so require you to produce a hi-res version of the logo for us too. There will be three individual business cards to produce with just the names and phone numbers being different. Address will change too, but use what you see on the card for now.

Industry/Entity Type

Business

Requirements
Nice to have
• You could consider a redesign to the new logo, just not too radical. We like the blue and green hexagons as we feel that they are representative of oil industry that we are in.

```html
<!DOCTYPE html>
<html lang="en">
<head>
<meta charset="utf-8">
<title>Verdan Oil Services – Business Card</title>
<link href="https://fonts.googleapis.com/css2?family=Open+Sans:wght@300;400;600;700&display=swap" rel="stylesheet">
<style>
  :root {
    --stage: #e9e7e2;
    --card-light: #ffffff;
    --card-shade: #e4e5e6;
    --back-dark: #3f4143;
    --back-mid: #6a6c6e;
    --ink: #4a4d50;
    --brand-green: #7cc242;
    --accent-orange: #f7941d;
    --arc-grey: #6d7073;
  }
  * { box-sizing: border-box; margin: 0; padding: 0; }
  html, body {
    width: 1200px; height: 677px; overflow: hidden;
    background: var(--stage);
    font-family: "Open Sans", Arial, sans-serif;
  }
  .canvas { position: relative; width: 1200px; height: 677px; }
  .card {
    position: absolute;
    width: 880px; height: 503px;
    overflow: hidden;
    box-shadow: 0 16px 36px rgba(0,0,0,0.25);
  }
  .card--back {
    left: 250px; top: 124px;
    background: linear-gradient(135deg, var(--back-dark) 0%, var(--back-mid) 55%, var(--back-dark) 100%);
  }
  .card--front {
    left: 70px; top: 50px;
    background: radial-gradient(ellipse at 45% 40%, var(--card-light) 0%, var(--card-light) 35%, var(--card-shade) 100%);
  }
  .card__arcs { position: absolute; inset: 0; }
  .brand {
    position: absolute; left: 92px; top: 64px;
    display: flex; align-items: center; gap: 18px;
  }
  .brand__square { width: 44px; height: 44px; background: var(--brand-green); }
  .brand__text { color: var(--ink); font-weight: 600; line-height: 1; }
  .brand__name { font-size: 76px; letter-spacing: -1px; }
  .brand__sub { font-size: 32px; margin-top: 6px; }
  .person { position: absolute; left: 322px; top: 236px; }
  .person__name {
    color: var(--brand-green); font-size: 25px; font-weight: 600;
    letter-spacing: 1px; text-transform: uppercase;
  }
  .person__title { color: var(--ink); font-size: 18px; margin-top: 2px; }
  .contact {
    position: absolute; right: 44px; top: 56px;
    list-style: none; text-align: right;
    color: var(--ink); font-size: 16px; line-height: 1.35;
  }
  .contact__item { display: flex; justify-content: flex-end; align-items: center; gap: 12px; margin-bottom: 12px; }
  .contact__item--address { align-items: flex-start; margin-bottom: 22px; }
  .contact__icon { width: 21px; height: 21px; flex: none; }
</style>
</head>
<body>
<main class="canvas">
  <div class="card card--back" aria-label="Card reverse side"></div>

  <article class="card card--front">
    <svg class="card__arcs" viewBox="0 0 880 503" aria-hidden="true">
      <circle cx="20" cy="335" r="118" fill="none" stroke="var(--arc-grey)" stroke-width="30"/>
      <circle cx="250" cy="555" r="192" fill="none" stroke="var(--brand-green)" stroke-width="32"/>
      <rect class="ring-marker" x="18" y="304" width="52" height="52" fill="var(--brand-green)"/>
      <rect class="ring-marker" x="212" y="414" width="62" height="62" fill="var(--brand-green)"/>
    </svg>

    <div class="brand">
      <span class="brand__square"></span>
      <div class="brand__text">
        <div class="brand__name">Verdan</div>
        <div class="brand__sub">Oil Services</div>
      </div>
    </div>

    <div class="person">
      <div class="person__name">Marcus Hale</div>
      <div class="person__title">Managing Director</div>
    </div>

    <ul class="contact">
      <li class="contact__item contact__item--address">
        <span>Level 4, 12 Harbour Street<br>Eastport</span>
        <svg class="contact__icon" viewBox="0 0 24 24"><path d="M12 2a7 7 0 0 0-7 7c0 5 7 13 7 13s7-8 7-13a7 7 0 0 0-7-7zm0 9.5A2.5 2.5 0 1 1 12 6.5a2.5 2.5 0 0 1 0 5z" fill="var(--brand-green)"/></svg>
      </li>
      <li class="contact__item">
        <span>021 555 0142</span>
        <svg class="contact__icon" viewBox="0 0 24 24"><path d="M6.6 10.8a15 15 0 0 0 6.6 6.6l2.2-2.2a1 1 0 0 1 1-.25 11.4 11.4 0 0 0 3.6.6 1 1 0 0 1 1 1V20a1 1 0 0 1-1 1A17 17 0 0 1 3 4a1 1 0 0 1 1-1h3.5a1 1 0 0 1 1 1 11.4 11.4 0 0 0 .6 3.6 1 1 0 0 1-.25 1z" fill="var(--brand-green)"/></svg>
      </li>
      <li class="contact__item">
        <span>021 555 0143</span>
        <svg class="contact__icon" viewBox="0 0 24 24"><rect x="6" y="2" width="12" height="20" rx="2" fill="var(--brand-green)"/><rect x="8" y="5" width="8" height="12" fill="#fff"/></svg>
      </li>
      <li class="contact__item">
        <span>021 555 0144</span>
        <svg class="contact__icon" viewBox="0 0 24 24"><rect x="3" y="8" width="18" height="10" rx="1" fill="var(--brand-green)"/><rect x="7" y="3" width="10" height="6" fill="var(--brand-green)"/><rect x="7" y="14" width="10" height="6" fill="#fff" stroke="var(--brand-green)" stroke-width="1.5"/></svg>
      </li>
      <li class="contact__item">
        <span>m.hale@verdanoil.com</span>
        <svg class="contact__icon" viewBox="0 0 24 24"><circle cx="12" cy="12" r="10" fill="var(--brand-green)"/><rect x="6.5" y="8" width="11" height="8" fill="#fff"/><path d="M6.5 8 12 12.5 17.5 8" fill="none" stroke="var(--brand-green)" stroke-width="1.2"/></svg>
      </li>
      <li class="contact__item">
        <span>www.verdanoil.com</span>
        <svg class="contact__icon" viewBox="0 0 24 24"><circle cx="12" cy="12" r="10" fill="var(--brand-green)"/><circle cx="12" cy="12" r="6" fill="none" stroke="#fff" stroke-width="1.5"/><path d="M6 12h12M12 6v12" stroke="#fff" stroke-width="1.5"/></svg>
      </li>
    </ul>
  </article>
</main>
</body>
</html>
```